Website Design for Stratovane Cloud As a Service

We are building a service to allow customers to own their own private clouds easily and cheaply. Owning your own private cloud saves costs, and offers more flexibility than a public cloud provider but has historically been a complex and expensive option.

We plan to offer a service where we build and maintain your own private cloud on your own hardware for a cheap monthly costs. Similar to this service - https://nimbrovex.com/solutions/private-cloud

We already have a logo and branding in place - we'd like a website design to be tailored from this branding, see attached logo design.

Feel free to add important elements on the home page such as testimonials, client/partner logos, contact form, social media, etc using placeholder contents in addition to the document we attached.

We also plan to add sub-pages in the future so please make sure that your website design has a full navigation menu.

An example of the site we like: https://www.quorvant.com/ we'd be happy for you to take inspiration from this website.

Target Market(s)

B2B focused, we are targeting start-up/small/medium sized companies who needs help with their cloud and IT infrastructure.

Industry/Entity Type

IT

Number of Pages Required

1 page

Font styles to use
Other font styles liked:
• Please refer to the attachment - font must have Mayeka Demi Bold & Retroica

Requirements
Must have
• Please add placeholder menu since we're planning to have subpages later on.

```html
<!DOCTYPE html>
<html lang="en">
<head>
<meta charset="utf-8">
<title>Stratovane Cloud — Private Cloud as a Service</title>
<link rel="stylesheet" href="https://fonts.googleapis.com/css2?family=Questrial&family=Comfortaa:wght@500;700&family=Poppins:wght@400;500;600&display=swap">
<style>
:root{
  --blue:#1a9be0;
  --blue-head:#2b88d0;
  --band:#2f5f96;
  --sky:#04a8ef;
  --ink:#111;
  --night:#0b0b0b;
  --white:#fff;
  --muted:#d8e6f3;
}
*{box-sizing:border-box;margin:0;padding:0}
html,body{width:1200px;height:4255px;overflow:hidden;background:var(--white)}
body{font-family:"Poppins",sans-serif;color:var(--ink);position:relative}
a{text-decoration:none}
.page{position:relative;width:1200px;height:4255px;overflow:hidden}
.abs{position:absolute}
.brand{display:flex;align-items:center;gap:10px;font-family:"Questrial",sans-serif;color:var(--blue-head);font-size:30px;white-space:nowrap}
.brand-dot{width:34px;height:34px;border-radius:50%;background:var(--blue)}
.btn{position:absolute;display:flex;align-items:center;justify-content:center;gap:12px;font-family:"Questrial",sans-serif;font-size:18px;letter-spacing:.3px;text-transform:uppercase}
.btn-icon{width:30px;height:20px;border-radius:10px;background:currentColor;opacity:.9}
.btn-fill{background:var(--blue);color:var(--white);box-shadow:0 4px 8px rgba(0,0,0,.18)}
.btn-line{border:2px solid var(--white);color:var(--white)}
/* header */
.site-header{left:0;top:0;width:1200px;height:71px;background:var(--white)}
.nav{left:437px;top:26px;font-family:"Poppins",sans-serif;font-weight:500;font-size:14px}
.nav a{color:var(--ink);position:absolute;white-space:nowrap}
.login{left:964px;top:20px;width:132px;height:38px;border:2px solid var(--blue);color:var(--ink);font-family:"Poppins",sans-serif;font-weight:500;font-size:15px}
.login .btn-icon{color:var(--blue)}
/* hero */
.hero{left:0;top:71px;width:1200px;height:664px;background:var(--night)}
.hero-photo{left:570px;top:53px;width:630px;height:611px;background:radial-gradient(ellipse at 55% 50%,#2a7fc4 0%,#1b4f80 40%,#101820 75%)}
.hero-title{left:104px;top:118px;width:450px;font-family:"Comfortaa",sans-serif;font-weight:500;font-size:33px;line-height:44px;color:var(--white)}
.hero-text{left:104px;top:316px;width:448px;font-size:13px;line-height:26px;font-weight:600;color:var(--white)}
.hero .btn{left:104px;top:429px;width:205px;height:56px}
/* section titles */
.section-title{font-family:"Questrial",sans-serif;color:var(--blue-head);font-size:50px;line-height:62px;text-transform:uppercase;letter-spacing:.5px}
.rule{height:3px;background:var(--blue)}
.benefits{left:102px;top:1020px;width:520px;list-style:none;font-size:17px;line-height:26px;font-weight:500}
.benefits li{margin-bottom:25px}
.photo{border-radius:16px;box-shadow:0 6px 14px rgba(0,0,0,.3)}
.frame{border:2px solid var(--blue);border-radius:18px}
/* band */
.band{left:0;top:1651px;width:1200px;height:612px;background:var(--band)}
.band-mark{left:570px;top:42px;width:60px;height:40px;border-radius:20px;background:var(--white)}
.band-title{left:0;top:100px;width:1200px;text-align:center;font-family:"Questrial",sans-serif;font-size:31px;color:var(--white)}
.band-text{left:190px;top:154px;width:820px;text-align:center;font-size:14px;line-height:26px;font-weight:600;color:var(--white)}
.node{width:100px;height:100px;border-radius:50%;background:var(--white);border:6px solid var(--band);box-shadow:0 0 0 2px var(--white);display:flex;align-items:center;justify-content:center}
.node-label{font-size:17px;font-weight:600;color:var(--white)}
.screen{left:489px;top:480px;width:216px;height:132px;background:var(--white);box-shadow:0 4px 10px rgba(0,0,0,.25);display:flex;align-items:center;justify-content:center}
.screen .brand{font-size:19px;gap:6px}
.screen .brand-dot{width:18px;height:18px}
.public-copy{left:607px;top:2675px;width:470px;font-size:16px;line-height:26px;font-weight:500}
.public-copy p{margin-bottom:26px}
/* difference */
.difference{left:353px;top:3332px;width:847px;height:478px;background:var(--sky);border-bottom-left-radius:200px;z-index:2}
.difference h2{position:absolute;left:50px;top:40px;font-family:"Questrial",sans-serif;font-size:49px;font-weight:400;color:var(--white)}
.difference p{position:absolute;left:61px;top:116px;width:735px;font-size:14px;line-height:25.6px;font-weight:600;color:var(--white)}
.difference .btn{left:66px;top:327px;width:205px;height:54px}
/* footer */
.site-footer{left:0;top:3764px;width:1200px;height:491px;background:var(--night);color:var(--white)}
.footer-about{left:102px;top:218px;width:430px;font-size:14px;line-height:26px}
.footer-head{font-family:"Questrial",sans-serif;font-size:21px;font-weight:400}
.footer-links{list-style:none;font-size:14px;font-weight:600;line-height:25px}
.footer-links li::before{content:"";display:inline-block;border-left:6px solid var(--white);border-top:4px solid transparent;border-bottom:4px solid transparent;margin-right:12px}
.contact-row{display:flex;align-items:center;gap:16px;font-size:14px;font-weight:600;line-height:26px}
.contact-icon{width:32px;height:32px;border:2px solid var(--white);border-radius:50%;flex:none;display:flex;align-items:center;justify-content:center}
.footer-rule{left:102px;top:404px;width:998px;height:1px;background:#555}
.copyright{left:102px;top:440px;font-size:13px;font-weight:600}
.social{top:438px;width:18px;height:18px;border-radius:50%;background:var(--white)}
.version{left:1150px;top:444px;font-size:10px}
</style>
</head>
<body>
<div class="page">

<header class="site-header abs">
  <div class="brand abs" style="left:102px;top:16px"><span class="brand-dot"></span>Stratovane Cloud</div>
  <nav class="nav abs">
    <a href="#" style="left:0">HOME</a>
    <a href="#" style="left:94px">ABOUT</a>
    <a href="#" style="left:198px">SERVICES</a>
    <a href="#" style="left:319px">BLOG</a>
    <a href="#" style="left:412px">CONTACT</a>
  </nav>
  <a class="btn login" href="#"><span class="btn-icon"></span>LOGIN</a>
</header>

<section class="hero abs">
  <div class="hero-photo abs" role="img" aria-label="Two colleagues reviewing work on a laptop in front of a blue cloud shape"></div>
  <h1 class="hero-title abs">A groundbreaking way for your small business to benefit from the power of the cloud</h1>
  <p class="hero-text abs">Stratovane Cloud as a Service is here to help small businesses utilise the power of the cloud without complicated set-ups or scary price tags.</p>
  <a class="btn btn-line" href="#"><span class="btn-icon"></span>CONTACT US</a>
</section>

<div class="rule abs" style="left:102px;top:874px;width:142px"></div>
<h2 class="section-title abs" style="left:266px;top:843px;width:720px">How SCAAS benefits your business</h2>
<ul class="benefits abs">
  <li>Totally flexible – get the cloud you want and the latest innovations you need</li>
  <li>Faster – our private cloud solutions outpace public clouds</li>
  <li>Greater value for money – totally transparent pricing for no nasty month-end surprises</li>
  <li>No consultancy fees – we'll work with you and charge set fees for everything</li>
  <li>Management, monitoring and maintenance – they're all included in your monthly price</li>
  <li>Tried and tested cloud solutions – we'll deploy the right OpenRack solutions for your business</li>
</ul>
<a class="btn btn-fill" href="#" style="left:104px;top:1489px;width:205px;height:56px"><span class="btn-icon"></span>LEARN MORE</a>
<div class="frame abs" style="left:690px;top:974px;width:439px;height:569px"></div>
<div class="photo abs" style="left:682px;top:987px;width:432px;height:573px;background:linear-gradient(160deg,#8fb3d6,#3b6b9c 50%,#1c3350)" role="img" aria-label="Engineer with a tablet in a server room"></div>

<section class="band abs">
  <div class="band-mark abs"></div>
  <h2 class="band-title abs">SCAAS CAN DRIVE YOUR DIGITAL TRANSFORMATION TODAY</h2>
  <p class="band-text abs">Organisations of all shapes and sizes are reaping the time and money saving benefits that the cloud brings. But for small businesses seeking to transition, managing the time and financial costs of transitioning, and knowing whether to opt for a public or private cloud can cause you to hit the pause button.SCAAS is here to help you switch on your cloud transformation in a way that works best for you. We deliver and support fully managed private cloud solutions that are</p>
  <svg class="abs" style="left:0;top:350px" width="1200" height="262" aria-hidden="true">
    <path d="M335 262 V180 Q380 70 466 58 Q600 0 712 60 Q810 90 855 190 V262" fill="none" stroke="#1d2f45" stroke-width="2"/>
  </svg>
  <div class="node abs" style="left:416px;top:358px"><svg width="50" height="40"><path d="M12 30 a10 10 0 0 1 2-19 a13 13 0 0 1 24 2 a8 8 0 0 1 0 17 Z" fill="none" stroke="#1a9be0" stroke-width="2.5"/></svg></div>
  <div class="node abs" style="left:662px;top:361px"><svg width="50" height="50" stroke="#222" stroke-width="3"><path d="M6 14h16M14 6v16M30 14h14M8 30l12 12M20 30L8 42M30 34h14M30 42h14"/></svg></div>
  <div class="node abs" style="left:288px;top:478px"><svg width="50" height="46" stroke="#222" stroke-width="2.5" fill="none"><path d="M6 44V30M16 44V24M26 44V18M36 44V12M4 26L20 14L30 18L46 4"/></svg></div>
  <div class="node abs" style="left:804px;top:488px"><svg width="50" height="50" fill="none" stroke="#222" stroke-width="3"><circle cx="25" cy="25" r="18"/><circle cx="25" cy="25" r="8"/></svg></div>
  <span class="node-label abs" style="left:340px;top:378px">Easy</span>
  <span class="node-label abs" style="left:802px;top:377px">Powerful</span>
  <span class="node-label abs" style="left:224px;top:516px">Fast</span>
  <span class="node-label abs" style="left:926px;top:524px">Scalable</span>
  <div class="screen abs"><div class="brand"><span class="brand-dot"></span>Stratovane Cloud</div></div>
</section>
<div class="abs" style="left:462px;top:2263px;width:270px;height:6px;background:#e0e0e0;border-radius:3px"></div>
<a class="btn btn-fill" href="#" style="left:499px;top:2329px;width:204px;height:49px"><span class="btn-icon"></span>GET STARTED</a>

<div class="rule abs" style="left:102px;top:2500px;width:142px"></div>
<h2 class="section-title abs" style="left:266px;top:2469px;width:720px">If you're using a public cloud now…</h2>
<div class="frame abs" style="left:94px;top:2636px;width:428px;height:567px"></div>
<div class="photo abs" style="left:109px;top:2650px;width:429px;height:572px;background:linear-gradient(200deg,#2a5d96,#14345a 55%,#0b1a2c)" role="img" aria-label="Developer typing at a desk with monitors showing code"></div>
<div class="public-copy abs">
  <p>You could be paying too much… Public cloud pricing structures have a habit of sneakily scaling up very quickly. With SCAAS, you'll always know what you're paying for your private cloud services.</p>
  <p>You're likely not getting the benefits of full functionality… Public cloud providers cannot adopt new innovations and functions as quickly and easily as the private cloud solutions you'll get from SCAAS.</p>
  <p>You'll be tied to the services your provider can provide… Public cloud providers will have a limited suite of products and services to offer you. A SCAAS private cloud has no such limitations</p>
</div>
<a class="btn btn-fill" href="#" style="left:621px;top:3129px;width:205px;height:53px"><span class="btn-icon"></span>LET'S TALK</a>

<div class="rule abs" style="left:152px;top:3397px;width:142px"></div>
<section class="difference abs">
  <h2>THE SCAAS DIFFERENCE</h2>
  <p>We'll quickly get to grips with what your organisation needs, and deliver it via our private cloud solutions.Enjoy the ease of the public cloud, combined with the features, innovations and flexibility of the private cloud.You can focus on your core business while we support you with a dedicated cloud infrastructure.We'll create and deliver the launchpad that will take your business forward.Get the benefits of your own cloud infrastructure and reduce your operational costs Fast and easy computing, storage and network resourcesManaged operations from private OpenRack clouds and KuberionWe'll support your growth and scale your cloud as you need it.</p>
  <a class="btn btn-line" href="#"><span class="btn-icon"></span>LET'S TALK</a>
</section>

<footer class="site-footer abs">
  <div class="brand abs" style="left:102px;top:130px;font-size:40px;gap:14px"><span class="brand-dot" style="width:48px;height:48px"></span>Stratovane Cloud</div>
  <p class="footer-about abs">Lorem ipsum dolor sit amet, consectetur adipiscing elit, sed do eiusmod tempor incididunt ut labore et dolore magna aliqua Ut enim ad minim veniam, quis nostrud exercitation ullamco laboris nisi ut aliquip ex ea commodo consequat</p>
  <h3 class="footer-head abs" style="left:594px;top:136px">Help Link</h3>
  <ul class="footer-links abs" style="left:594px;top:176px">
    <li>Terms&amp;condtions</li><li>Privacy Policy</li><li>About Us</li><li>Support</li>
  </ul>
  <h3 class="footer-head abs" style="left:594px;top:310px">Email</h3>
  <a class="abs" href="#" style="left:594px;top:340px;font-size:14px;font-weight:600;color:var(--blue)">info@stratovane.com</a>
  <h3 class="footer-head abs" style="left:825px;top:132px">Our Location</h3>
  <div class="contact-row abs" style="left:822px;top:180px;width:300px"><span class="contact-icon"><svg width="14" height="18"><path d="M7 17C2 10 1 8 1 6a6 6 0 0 1 12 0c0 2-1 4-6 11Z" fill="none" stroke="#fff" stroke-width="1.6"/></svg></span><span>4000 Lorem ipsum dolor sit amet, consectetur adipiscing</span></div>
  <div class="contact-row abs" style="left:822px;top:255px"><span class="contact-icon"><svg width="16" height="16"><path d="M3 1l3 1 1 4-2 1a9 9 0 0 0 4 4l1-2 4 1 1 3-2 2C7 15 1 9 1 3Z" fill="none" stroke="#fff" stroke-width="1.4"/></svg></span><span>+1 555-014-2290</span></div>
  <div class="contact-row abs" style="left:822px;top:313px"><span class="contact-icon"><svg width="16" height="12"><rect x="1" y="1" width="14" height="10" fill="none" stroke="#fff" stroke-width="1.4"/><path d="M1 1l7 6 7-6" fill="none" stroke="#fff" stroke-width="1.4"/></svg></span><span>info@stratovane.com</span></div>
  <div class="footer-rule abs"></div>
  <p class="copyright abs">© copyrights 2022 stratovane | All Rights Reserved</p>
  <span class="social abs" style="left:934px"></span>
  <span class="social abs" style="left:981px"></span>
  <span class="social abs" style="left:1029px"></span>
  <span class="social abs" style="left:1077px"></span>
  <span class="version abs">C 25</span>
</footer>

</div>
</body>
</html>
```